Website and Logo Design for new niche job board.

Hello, We are an up and coming job board that is focused on LEGITIMATE companies that hire telecommuters to work from home. We are looking to build a highly interactive job board and forum/blog. The site is called TaskHarbor.com We focus on helping work at home moms, older workers and college students in work at home positions. We offer free job posting and advertising to the employer and free resume posting to the job seeker. (Free everything basically) Our revenue will be based from banner ads on the site so we will need a space on both sides of the page for those ads. 

The software we are using to build the job board part of the site can be viewed at www.plinkforge.example. It is already built! We do not need job software but a dashboard look to our main page - PLEASE pay attention to this! Do not submit a job board look as we have the job board page built!

These are the sites I like - please use these links to understand exactly the look I want

 

http://www.brightmuffins.example/

http://www.evagrant.example/

http://www.ladiesatwork.example/

https://www.findingnannies.example/index.asp?
Updates

Hi everyone- I think there might be some confusion to what we are looking for. We have the job board software through www.plinkforge.example, we are looking for the main page to be built around that. Basically we want a dashboard look with lots of little boxes to add content such as different articles,podcasts, forums,blogs,highlight different companies hiring,etc. If you can add scrolling or moving objects would be ideal. The less of a static website the better. You dont have to worry about the jobboard portion just the main page when you click on www.TaskHarbor.com, we really need it to capture peoples attention and see its a staffing firm AND a job board, forum, etc for work at home positions.  Here are some looks I am aiming for -

http://www.evagrant.example/

Please use alot of color- lime green, oranges, turquiose blue, purple, lots and lots of color please! I like more tropical colors. Thanks! I dont like red and dark colors at all. Thanks

Target Market(s)

Target customers will be both companies and individuals. The individuals will be a broad age range that are interested in working from home. The companies will be small to large corporations that have valid work from home positions.

Requirements
Must have
• I want a colorful site with moving objects and scrolling text - static sites are bland, and outdated- I am looking for a HIGHLY interactive board. Please do not just throw a template up there and expect me to like it. I am picky and want an ultra sleek design and eye catching. I can make an out of the box website myself, I have 3 other companies and did that -  PLEASE PLEASE DO NOT SHOW ME A COOKIE!
Nice to have
• Would be very nice to have the HTML sliced up for finished designs.
Should not have
• just not boring and static. Anything new and creative is where we are heading.

```html
<!DOCTYPE html>
<html lang="en">
<head>
<meta charset="utf-8">
<title>TaskHarbor – Work From Home Jobs</title>
<link href="https://fonts.googleapis.com/css2?family=Arimo:wght@400;700&display=swap" rel="stylesheet">
<style>
:root{
  --sky-top:#5f9fd6; --sky-mid:#a9cdea; --sky-low:#e4eef4;
  --lime:#8cc21e; --lime-dark:#5f9a0e; --lime-light:#b9e05a;
  --navy:#0f2238; --ink:#222; --muted:#555;
  --hero-box:rgba(38,78,128,.88);
  --tab-dark:#151515; --panel-grey:#8d8d8d;
  --cream:#efefdc; --row:#e4e8ee;
  --maroon:#7a1010; --band-top:#76b3ec; --band-low:#2f5f98;
  --forum:#7fa5bd; --white:#fff;
}
*{box-sizing:border-box;margin:0;padding:0}
html,body{width:1091px;height:1200px;overflow:hidden;background:var(--white)}
body{font-family:"Arimo",Arial,sans-serif;color:var(--ink);position:relative;font-size:11px}
.abs{position:absolute}
a{color:inherit;text-decoration:none}
h1,h2,h3{font-weight:400}

/* header */
.header{left:0;top:0;width:1091px;height:367px;background:linear-gradient(180deg,var(--sky-top) 0%,var(--sky-mid) 55%,var(--sky-low) 100%);overflow:hidden}
.hero-photo{left:110px;top:28px;width:600px;height:339px;background:radial-gradient(ellipse at 62% 40%,#e9d2b4 0%,#c9a98a 22%,rgba(150,150,160,.6) 45%,rgba(120,160,200,0) 70%);}
.hill{left:50px;top:300px;width:300px;height:70px;background:radial-gradient(ellipse at 50% 0%,var(--lime-light),var(--lime-dark));border-radius:50% 50% 0 0}
.brand{left:58px;top:58px;display:flex;align-items:center;gap:8px}
.brand-dot{width:20px;height:20px;border-radius:50%;background:var(--lime)}
.brand-name{font-weight:700;font-size:34px;color:#2e4a12;letter-spacing:-.5px}
.callout{left:72px;top:284px;color:var(--white);font-weight:700;font-size:16px;white-space:nowrap}
.phone{left:80px;top:310px;color:var(--white);font-weight:700;font-size:29px;white-space:nowrap}
.toplinks{left:780px;top:60px;color:var(--white);font-size:10px;white-space:nowrap}
.lang{left:940px;top:57px;width:79px;height:16px;background:var(--white);border:1px solid #999;font-size:11px;padding-left:3px;line-height:14px}
.lang::after{content:"";position:absolute;right:4px;top:5px;border:4px solid transparent;border-top-color:#000}
.hero-box{left:702px;top:111px;width:318px;height:215px;background:var(--hero-box);color:var(--white);padding:24px 16px}
.hero-box h1{font-size:21px;line-height:27px;font-weight:700}
.hero-box p{font-size:10px;line-height:16px;margin-top:10px;text-align:justify;letter-spacing:.3px}
.pill{position:absolute;background:linear-gradient(#d6d6d6,#8d8d8d);color:var(--white);border-radius:9px;font-weight:700;font-size:8px;text-align:center;line-height:16px;height:16px;white-space:nowrap}
.hero-box .pill{left:203px;top:180px;width:68px}
.nav{top:338px;height:29px;display:flex;align-items:center;justify-content:center;color:var(--white);font-weight:700;font-size:13px;background:var(--tab-dark);white-space:nowrap}
.nav.home{background:linear-gradient(var(--lime-light),var(--lime));}
.caret{margin-left:4px;border:4px solid transparent;border-top-color:#aaa;margin-top:4px}

/* sidebar search */
.tab{top:389px;height:16px;font-size:10px;line-height:16px;text-align:center;color:#444}
.tab.on{left:53px;width:97px;background:#a7a7a7}
.tab.off{left:155px;width:111px;background:#f2f2f2;border:1px solid #ddd;color:#777}
.search-panel{left:43px;top:405px;width:230px;height:269px;background:linear-gradient(#9b9b9b,#7d7d7d);padding:0 19px}
.search-panel label{display:block;font-size:11px;font-weight:700;color:#1a1a1a;margin-top:8px}
.search-panel label.plain{font-weight:400}
.field{background:var(--white);height:21px;border:1px solid #777;font-size:15px;line-height:20px;padding-left:4px;position:relative;margin-top:3px}
.field.select::after{content:"";position:absolute;right:4px;top:9px;border:4px solid transparent;border-top-color:#000}
.btn-search{display:inline-block;margin-top:12px;background:linear-gradient(#fff,#ddd);border:1px solid #777;font-size:15px;padding:2px 10px}

.heading{display:flex;align-items:center;gap:12px;font-size:18px;color:#444;font-weight:400;white-space:nowrap}
.heading::before{content:"";width:10px;height:10px;border-radius:50%;background:var(--lime)}
.on-blue{color:var(--white);font-size:22px}
.featured-box{left:45px;top:732px;width:219px;height:86px;border:1px solid #999;display:flex;align-items:center;justify-content:center;gap:8px;font-size:25px;color:#1f2b3a}
.featured-box span{width:18px;height:18px;background:#1f6fb3;border-radius:50%}

/* center */
.banner{left:299px;top:395px;width:519px;height:113px;border:1px solid #999;overflow:hidden}
.banner-art{left:14px;top:10px;width:300px;height:95px;background:radial-gradient(ellipse at 50% 55%,#c9632a 0%,#6b5a4a 35%,#d8d8d8 65%,rgba(255,255,255,0) 80%)}
.banner-title{left:348px;top:32px;font-size:27px;color:#1a2a5a;white-space:nowrap}
.banner-url{left:352px;top:65px;font-size:12px;color:#1a2a5a;white-space:nowrap}
.banner-rule{left:300px;top:86px;width:212px;height:2px;background:#8a6a3a}

.jobs{left:296px;top:522px;width:525px;height:323px;background:var(--cream)}
.jobs-search{left:635px;top:538px;width:136px;height:20px;border:2px solid #bbb;border-radius:10px;background:var(--white);font-style:italic;font-size:10px;padding-left:12px;line-height:17px}
.go{left:781px;top:533px;width:26px;height:26px;border-radius:50%;background:radial-gradient(#4a7a3a,#1f3d18)}
.job-row{position:absolute;left:296px;width:516px;font-size:11px}
.job-row .bg{position:absolute;left:49px;top:0;width:467px;height:36px;background:var(--row)}
.job-row .line{position:absolute;left:49px;top:43px;width:467px;height:1px;background:#ccc}
.job-row span{position:absolute;white-space:nowrap}
.job-title{color:var(--maroon)}
.total{font-style:italic;font-size:10px;color:#666;white-space:nowrap}
.btn-green{background:linear-gradient(var(--lime-light),var(--lime-dark));color:var(--white);border-radius:9px;font-size:12px;text-align:center;line-height:34px;height:34px;width:119px}

/* right */
.hired{left:833px;top:393px;width:207px;height:201px;background:linear-gradient(#fff,#ececec)}
.hired ul{list-style:none;position:absolute;left:20px;top:40px;font-size:10.5px}
.hired li{height:27px;display:flex;align-items:flex-start;gap:8px;white-space:nowrap}
.hired li::before{content:"";width:0;height:0;border-top:4px solid transparent;border-bottom:4px solid transparent;border-left:6px solid #999;margin-top:2px;flex:none}
.hired .pill{left:132px;top:172px;width:69px}
.forum{left:845px;top:608px;width:183px;height:67px;background:var(--forum);border-radius:10px;color:var(--white);text-align:center}
.forum small{display:block;font-size:8px;margin-top:12px}
.forum strong{display:flex;justify-content:center;align-items:center;gap:12px;font-size:24px;font-weight:400;margin-top:4px}
.forum i{width:20px;height:20px;border-radius:50%;background:var(--lime);display:inline-block}
.badges{left:858px;top:735px;width:160px;height:90px}
.badge{position:absolute;background:#1a1a1a;border-radius:3px}

/* band */
.band{left:0;top:865px;width:1091px;height:278px;background:linear-gradient(var(--band-top),var(--band-low))}
.thumb{top:945px;width:57px;height:57px;border:2px solid var(--white)}
.social{left:82px;top:1030px;display:flex;align-items:center;gap:10px;color:var(--white);font-weight:700;font-size:26px}
.social i{width:38px;height:38px;background:#3b5b9a;border:2px solid #dde;border-radius:4px}
.blog-img{left:310px;top:945px;width:152px;height:112px;border:4px solid var(--white);background:linear-gradient(135deg,#9db7d6,#36557d 55%,#c9d6e4)}
.blog-title{left:487px;top:944px;color:#ffe21a;font-size:17px;white-space:nowrap}
.blog-text{left:487px;top:978px;width:320px;color:var(--white);font-size:14px;line-height:22px;text-align:justify}
.blog-bar{left:304px;top:1086px;width:420px;height:22px;background:#888;border-radius:4px;color:var(--white);font-style:italic;font-size:10px;line-height:22px;padding-left:13px}
.podcast{left:845px;top:950px;width:195px;height:87px;background:linear-gradient(90deg,#d8dde2,#f1f0e2)}
.podcast .pic{position:absolute;left:8px;top:3px;width:80px;height:80px;background:linear-gradient(#f0d8b0,#b9c6d6)}
.podcast .who{position:absolute;left:108px;top:33px;font-size:11px;white-space:nowrap}
.podcast .play{position:absolute;left:115px;top:50px;width:52px;height:13px;background:#f2cc2b;border:1px solid #a8841a;font-size:9px;font-weight:700;text-align:center;line-height:12px}
.caption{left:855px;top:1049px;color:var(--white);font-size:11px;white-space:nowrap}

.footer{left:0;top:1143px;width:1091px;height:57px;background:var(--navy);color:var(--white);font-size:10.5px}
.footer .copy{position:absolute;left:87px;top:24px}
.footer .links{position:absolute;right:63px;top:24px;white-space:nowrap}
</style>
</head>
<body>

<header class="header abs">
  <div class="hero-photo abs" role="img" aria-label="Photo of a smiling woman holding a hire-me sign in front of a suburban house"></div>
  <div class="hill abs"></div>
  <div class="brand abs"><span class="brand-dot"></span><span class="brand-name">TASKHARBOR</span></div>
  <div class="callout abs">Call Us now to find out more!</div>
  <div class="phone abs">0800 555 0142</div>
  <nav class="toplinks abs">Home &nbsp;|&nbsp; Login &nbsp;|&nbsp; Contact Us</nav>
  <div class="lang abs">English</div>
  <section class="hero-box abs">
    <h1>Lorem ipsum dolor sit amet, consectetur adipiscing elit.</h1>
    <p>Lorem Ipsum is simply dummy text of the printing and typesetting industry. Lorem Ipsum has been the industry's standard dummy text ever since the 1500s, when an unknown printer took a galley of type and scrambl</p>
    <a class="pill" href="#">Read More</a>
  </section>
  <a class="nav home abs" style="left:436px;width:72px" href="#">Home</a>
  <a class="nav abs" style="left:513px;width:107px" href="#">My Account<span class="caret"></span></a>
  <a class="nav abs" style="left:627px;width:96px" href="#">Find Jobs<span class="caret"></span></a>
  <a class="nav abs" style="left:729px;width:117px" href="#">Post Resume</a>
  <a class="nav abs" style="left:853px;width:88px" href="#">Register</a>
  <a class="nav abs" style="left:948px;width:93px" href="#">Employer</a>
</header>

<div class="tab on abs">Quick Search</div>
<div class="tab off abs">Advanced Search</div>
<form class="search-panel abs">
  <label style="margin-top:0">Enter Keywords</label>
  <div class="field" style="width:179px;height:25px;margin-top:6px"></div>
  <label>Select Job Type</label><div class="field select">All Categories</div>
  <label>Select Country</label><div class="field select">All Countries</div>
  <label class="plain">Select State</label><div class="field select">All States</div>
  <label class="plain">Select City</label><div class="field select">All Cities</div>
  <span class="btn-search">Search</span>
</form>

<h2 class="heading abs" style="left:48px;top:698px">Featured Employee</h2>
<div class="featured-box abs"><span></span>BrightStudio</div>
<p class="abs" style="left:92px;top:827px">Total Job Offer: 56 Jobs</p>

<div class="banner abs">
  <div class="banner-art abs" role="img" aria-label="Three cars parked side by side"></div>
  <div class="banner-title abs">Rent A Car?</div>
  <div class="banner-url abs">visit www.driveleasy.example</div>
  <div class="banner-rule abs"></div>
</div>

<section class="jobs abs"></section>
<h2 class="heading abs" style="left:306px;top:535px;font-size:22px">Latest Job</h2>
<div class="jobs-search abs">Search</div>
<div class="go abs"></div>

<div class="job-row" style="top:574px"><div class="bg"></div><div class="line"></div>
  <span style="left:14px;top:7px">Apr 6</span><span class="job-title" style="left:58px;top:3px">Sr. Account Executive</span><span style="left:58px;top:17px">Lorem ipsum dolor sit amet, consectetur</span><span style="left:291px;top:12px">Boston</span><span style="left:357px;top:13px">Tech</span><span style="left:420px;top:13px">Not Specified</span></div>
<div class="job-row" style="top:617px"><div class="line"></div>
  <span style="left:14px;top:7px">Apr 4</span><span class="job-title" style="left:58px;top:3px">Field Agent</span><span style="left:58px;top:17px">Lorem ipsum dolor sit amet, consectetur</span><span style="left:291px;top:12px">Tulsa</span><span style="left:357px;top:13px">Medical</span><span style="left:420px;top:13px">20.00 Per Hour</span></div>
<div class="job-row" style="top:660px"><div class="bg"></div><div class="line"></div>
  <span style="left:14px;top:7px">Apr 1</span><span class="job-title" style="left:58px;top:3px">Secretary</span><span style="left:58px;top:17px">Lorem ipsum dolor sit amet, consectetur</span><span style="left:291px;top:12px">LA</span><span style="left:357px;top:13px">Student</span><span style="left:420px;top:13px">400,00 Per Year</span></div>
<div class="job-row" style="top:703px"><div class="line"></div>
  <span style="left:14px;top:7px">Mar 29</span><span class="job-title" style="left:58px;top:3px">Nurse</span><span style="left:58px;top:17px">Lorem ipsum dolor sit amet, consectetur</span><span style="left:291px;top:12px">New York</span><span style="left:357px;top:13px">Admin</span><span style="left:420px;top:13px">250.00 Per Hour</span></div>
<div class="job-row" style="top:746px"><div class="bg"></div>
  <span style="left:14px;top:7px">Mar 15</span><span class="job-title" style="left:58px;top:3px">Admin Staff</span><span style="left:58px;top:17px">Lorem ipsum dolor sit amet, consectetur</span><span style="left:291px;top:12px">Chicago</span><span style="left:357px;top:13px">Misc</span><span style="left:420px;top:13px">500.00 Per Month</span></div>
<p class="total abs" style="left:342px;top:800px">Total Available Job: 546 Jobs</p>
<a class="btn-green abs" style="left:694px;top:799px" href="#">View More</a>

<aside class="hired abs">
  <h2 class="heading abs" style="left:8px;top:6px">Latest Hired</h2>
  <ul>
    <li>Dora Linfield - Milwaukee</li>
    <li>Dana Rowe - Los Angeles</li>
    <li>Marla Denton - Chicago</li>
    <li>Nadia Kress - Denver</li>
    <li>Jalen Orford - Tenesse</li>
  </ul>
  <a class="pill" href="#">Read More</a>
</aside>
<a class="forum abs" href="#"><small>Join the most active discussion!</small><strong><i></i>FORUM</strong></a>
<h2 class="heading abs" style="left:841px;top:700px">Recognition</h2>
<div class="badges abs">
  <div class="badge" style="left:0;top:0;width:45px;height:22px"></div>
  <div class="badge" style="left:52px;top:0;width:50px;height:22px;background:#6db52c"></div>
  <div class="badge" style="left:108px;top:0;width:52px;height:22px"></div>
  <div class="badge" style="left:28px;top:46px;width:32px;height:36px;background:#888"></div>
  <div class="badge" style="left:66px;top:46px;width:36px;height:36px;border-radius:50%"></div>
  <div class="badge" style="left:112px;top:42px;width:22px;height:42px;background:#d83a2a"></div>
</div>

<section class="band abs"></section>
<h2 class="heading on-blue abs" style="left:42px;top:897px">Testimonial</h2>
<div class="thumb abs" style="left:68px;background:linear-gradient(#4a6f9a,#e2a86a)" role="img" aria-label="Portrait of a construction worker"></div>
<div class="thumb abs" style="left:130px;background:linear-gradient(#f5d0a8,#e69a5a)" role="img" aria-label="Portrait of a smiling girl"></div>
<div class="thumb abs" style="left:193px;background:linear-gradient(#7a5a3a,#d6aa88)" role="img" aria-label="Portrait of a smiling woman"></div>
<div class="social abs"><i></i>Socialnest</div>

<h2 class="heading on-blue abs" style="left:306px;top:897px">Featured Blog</h2>
<div class="blog-img abs" role="img" aria-label="Business handshake in front of office towers"></div>
<h3 class="blog-title abs">Lorem ipsum dolor sit amet</h3>
<p class="blog-text abs">Lorem ipsum dolor sit amet, consectetur adipiscing elit. Vestibulum ultricies, mauris quis pretium cursus, dui purus dapibus lorem, sodales convallis urna sem n</p>
<div class="blog-bar abs">Total Blog: 12 Blog</div>
<a class="btn-green abs" style="left:694px;top:1078px" href="#">View More</a>

<h2 class="heading abs" style="left:843px;top:910px;color:#fff;font-size:17px">Featured Podcast</h2>
<div class="podcast abs">
  <div class="pic" role="img" aria-label="News anchor portrait"></div>
  <span class="who">Janelle Ashby</span>
  <span class="play">▶ PLAY</span>
</div>
<p class="caption abs">consectetur adipiscing elit. dsadsa</p>

<footer class="footer abs">
  <span class="copy">Copyright 2010, www. TaskHarbor.com, all right reserved</span>
  <span class="links">FAQ | SITEMAP | &nbsp;POLICY &nbsp;| &nbsp;FIND JOBS | POST RESUME| REGISTER</span>
</footer>

</body>
</html>
```